Clear Plastic Card Design

I am looking to have a business card designed from my logo icon. I am looking to match the style of a different business card I have attached in the files.
Looking for a card that is plastic, with layers of transparency in the shape of my logo icon (also attached in the files) - not a circle like the other card. The winning design will incorporate the red icon logo on the front and back and include the charity's name, "Light for the Weary Souls" in the same or similar font, as well as an email and phone number. For now, use the email: email@lightfortheweary-mail.org and the phone number 555-382-7194.
We like how the sample business card has transparency, partial and full opacity layers and a matching color scheme. Files will need to be in vector so that our business card printing company can work with it.
UPDATE:
We've some excellent designs in, thank you everyone! I got an early review from the owner, and he requested a minor redirect to find his perfect design. He wants the design to stand out by NOT being a rectangle. Try instead a circle, square, or best yet - something that falls in the outline of the logo icon, either fully or partially. Thank you, everyone!
Light for the Weary Souls text should be incorporated as well as a phone and email.

```html
<!DOCTYPE html>
<html lang="en">
<head>
<meta charset="utf-8">
<title>Light for the Weary Souls – Business Cards</title>
<link rel="stylesheet" href="https://fonts.googleapis.com/css2?family=Poppins:wght@400;700&display=swap">
<style>
  :root {
    --page: #ffffff;
    --card-top: #fdf4ef;
    --card-mid: #fbe1d6;
    --card-bottom: #f6d2d3;
    --edge: #e85a5c;
    --edge-soft: #f08a6a;
    --brand-red: #e02a2a;
    --brand-pink: #d8204a;
    --ink: #111111;
  }
  html, body {
    margin: 0;
    padding: 0;
    width: 1200px;
    height: 1200px;
    overflow: hidden;
    background: var(--page);
  }
  .sheet { display: block; width: 1200px; height: 1200px; }
  .card { filter: drop-shadow(6px 8px 8px rgba(0,0,0,0.14)); }
  .card-panel { fill: url(#cardFill); stroke: var(--edge); stroke-width: 0.8; }
  .card-bridge { fill: #fbe6de; }
  .card-ring { fill: none; stroke: var(--edge-soft); stroke-width: 0.7; }
  .mark-disc { fill: var(--brand-red); }
  .brand-square { fill: var(--brand-red); }
  .text { font-family: "Poppins", sans-serif; }
  .brand-name { font-size: 15px; fill: var(--ink); }
  .brand-name--small { font-size: 12px; }
  .headline { font-size: 35px; fill: var(--ink); }
  .headline--accent { fill: var(--brand-red); font-weight: 400; }
  .person-name { font-size: 25px; font-weight: 700; fill: var(--brand-pink); }
  .person-role { font-size: 21px; fill: var(--ink); }
  .contact { font-size: 16px; fill: var(--ink); letter-spacing: 0.3px; }
  .icon-ring { fill: #fbe4dc; stroke: #e9a0a0; stroke-width: 0.8; }
  .icon-glyph { fill: var(--brand-red); }
</style>
</head>
<body>
<svg class="sheet" viewBox="0 0 1200 1200" xmlns="http://www.w3.org/2000/svg">
  <defs>
    <linearGradient id="cardFill" x1="0" y1="0" x2="0" y2="1">
      <stop offset="0" stop-color="var(--card-top)"/>
      <stop offset="0.5" stop-color="var(--card-mid)"/>
      <stop offset="1" stop-color="var(--card-bottom)"/>
    </linearGradient>
    <g id="cardShape">
      <rect class="card-bridge" x="636" y="217" width="66" height="152"/>
      <path class="card-panel" d="M639 125 H322.5 A80 80 0 0 0 242.5 205 V465 A80 80 0 0 0 322.5 545 H639 Z"/>
      <path class="card-panel" d="M699 125 H768 A210 210 0 0 1 768 545 H699 Z"/>
      <path class="card-ring" d="M699 149 H768 A186 186 0 0 1 768 521 H699"/>
      <path class="card-ring" d="M699 169 H768 A166 166 0 0 1 768 501 H699"/>
      <circle class="mark-disc" cx="748" cy="339" r="140"/>
    </g>
  </defs>

  <!-- Front -->
  <g class="card card--front">
    <use href="#cardShape"/>
    <rect class="brand-square" x="306" y="258" width="16" height="16"/>
    <text class="text brand-name" x="330" y="272">Light for the Weary Souls</text>
    <text class="text headline" x="305" y="388">Light for the</text>
    <text class="text headline headline--accent" x="305" y="422">Weary Souls</text>
  </g>

  <!-- Back -->
  <g class="card card--back" transform="translate(0 537.5)">
    <use href="#cardShape"/>
    <rect class="brand-square" x="306" y="220" width="13" height="13"/>
    <text class="text brand-name brand-name--small" x="325" y="231">Light for the Weary Souls</text>
    <text class="text person-name" x="306" y="337">Dana Morrow</text>
    <text class="text person-role" x="306" y="365">Marketing Director</text>

    <g class="contact-row">
      <circle class="icon-ring" cx="317" cy="413" r="11"/>
      <path class="icon-glyph" d="M312.5 406.5 l2.6-0.8 1.6 3.4-1.6 1.2 c0.7 1.8 2 3.2 3.7 4l1.3-1.5 3.3 1.7-0.9 2.6 c-5.4 0.2-10-4.5-10-10.6z"/>
      <text class="text contact" x="344" y="419">555-382-7194</text>
    </g>
    <g class="contact-row">
      <circle class="icon-ring" cx="317" cy="453" r="11"/>
      <rect class="icon-glyph" x="310.5" y="448.5" width="13" height="9" rx="1"/>
      <path d="M310.8 449 L317 454 L323.2 449" fill="none" stroke="#fbe4dc" stroke-width="1.2"/>
      <text class="text contact" x="346" y="458">email@lightfortheweary-mail.org</text>
    </g>
  </g>
</svg>
</body>
</html>
```